Im want a website LIKE VRX's and FleetHollow.com's with product payment options like Trenzo's

I need a website LIKE VRX with a header made EXACTLY LIKE THAT OF FLEETHOLLOWS .

The front page photo should be like that of FLEETHOLLOW's webpage as well.

The name of the website will be called "M.K. (Caldera Key)".

We will be targeting ALL MARKETS in a small town in central Panama and charging businesses "listing fees" like a phone book does but also providing informational blogs, news, and other interesting activities.

THIS IS A MULTI PAGE WEBSITE

THIS IS WHERE VRX's website meets Brivelle/FleetHollow.

Once the layout is built I will tweak and modify, add information, and upload items for sale.

Here is a list of specific categories that should be listed out above the front page header image/search bar

-- Home -- News -- Travel -- Activities -- Shop & Dine -- Store -- More... --

These categories should be spread across the bottom of the page in three sections:

WHATS SO GREAT ABOUT (Caldera Key),
HAND PICKED TOURS
ACTIVITIES etc.

Also lets use www.Trenzo.example 's
"HOT DESTINATIONS"
"BEAT THE BEST PRICES IN BOQUETE"
"OCTOBERS INSIDER PICKS"
"TOP DESTINATIONS"
and spread them in four sections side-by-side near the bottom of the page.

Overall I would like to see the finished product to be something LIKE VRX's and FleetHollows.

WE NEED ONLINE PAYMENT OPTIONS LIKE BRIVELLE'S WEBSITE HAS

This will be a desktop website but should be very mobile friendly as well.

-rodmund

P.S. Good luck!

If it isn't already too late to change the website name, the name of the website should be "Caldera Key". Added Friday, October 9, 2015

What do you guys think the budget should be to win this? Added Saturday, October 10, 2015

www.palmorra.example is the most amazing simple site. Whoever can make me a replica with my specifications will win immediately!!!! Added Sunday, October 18, 2015

OMG www.palmorra.example is the bomb!So simple and elegant. Whoever can make me an EXACT REPLICA OF WWW.PALMORRA.EXAMPLE as my site with the specifications mentioned in my brief will take home the $825.00 immediately! Good luck amigos! Added Sunday, October 18, 2015

Does anybody know how to add recurring monthly billing options on this website? Added Sunday, October 18, 2015

ALL MARKETS

Product

Coded - Design and coding required

5+ page

• Coinvey payment options.
• I must be able to add and remove photos/text and video from the HTML files in the page.
• Be creative my friends, and may the odds be forever in your favor!
• I added some photos of a good layout for our page below.

```html
<!DOCTYPE html>
<html lang="en">
<head>
<meta charset="utf-8">
<title>Caldera Key</title>
<link href="https://fonts.googleapis.com/css2?family=Oswald:wght@400;500;600&family=Open+Sans:wght@400;600;700&display=swap" rel="stylesheet">
<style>
:root{
  --blue:#1e9bd7;
  --blue-dark:#1580b5;
  --blue-deep:#0f6d9c;
  --ink:#333c44;
  --muted:#7d8790;
  --line:#e3e8ec;
  --page:#eef3f6;
  --white:#ffffff;
  --green:#7cc142;
  --orange:#f5a623;
}
*{box-sizing:border-box;margin:0;padding:0}
html,body{width:1200px;height:2252px;overflow:hidden}
body{position:relative;background:var(--page);font-family:'Open Sans',Arial,sans-serif;color:var(--ink);font-size:12px;line-height:1.55}

/* hero */
.hero{position:absolute;left:0;top:0;width:1200px;height:620px}
.hero-photo{position:absolute;inset:0;background:linear-gradient(180deg,#5fb4e4 0%,#7cc9ec 35%,#3cbcc6 60%,#56c9c9 80%,#8fded6 100%)}
.topbar{position:absolute;top:28px;right:40px;display:flex;gap:10px}
.select{height:24px;padding:0 10px;border:1px solid rgba(255,255,255,.7);color:var(--white);font-size:10px;line-height:22px;display:flex;align-items:center;gap:10px}
.logo{position:absolute;left:40px;top:40px;font-family:'Oswald',Arial,sans-serif;font-size:34px;font-weight:500;color:var(--white);letter-spacing:1px}
.nav{position:absolute;right:40px;top:66px;display:flex;gap:30px}
.nav a{color:var(--white);text-decoration:none;font-family:'Oswald',Arial,sans-serif;font-size:12px;letter-spacing:.6px;text-transform:uppercase;padding-bottom:6px}
.nav a.active{border-bottom:2px solid var(--white)}
.welcome{position:absolute;left:0;right:0;top:372px;text-align:center;color:var(--white)}
.welcome h1{font-family:'Oswald',Arial,sans-serif;font-weight:500;font-size:44px;letter-spacing:1px;text-transform:uppercase}
.welcome p{font-family:'Oswald',Arial,sans-serif;font-size:20px;text-transform:uppercase;letter-spacing:.8px;margin-top:4px}

/* main panel */
.panel{position:absolute;left:40px;top:606px;width:1120px;height:1222px;background:var(--white)}
.cards{position:absolute;left:22px;top:50px;display:flex;gap:20px}
.card{width:345px;height:372px;border:1px solid var(--line);position:relative}
.card h3{font-family:'Oswald',Arial,sans-serif;font-size:13px;font-weight:500;color:var(--blue);text-transform:uppercase;position:absolute;top:-26px;left:0;line-height:20px}
.card-photo{height:150px}
.card p{padding:14px 14px 0;color:var(--muted);font-size:11.5px}
.card-meta{padding:6px 14px 0;font-size:10px;color:var(--muted);display:flex;align-items:center;gap:6px}
.bar{margin:10px 14px 0;height:4px;background:var(--line);position:relative}
.bar span{position:absolute;left:0;top:0;height:4px}
.stats{position:absolute;left:0;right:0;bottom:0;height:52px;border-top:1px solid var(--line);display:flex;align-items:center}
.stat{flex:1;text-align:center;font-size:10px;color:var(--muted);line-height:1.3}
.stat b{display:block;color:var(--ink);font-size:12px}
.details{width:70px;margin-right:12px;height:26px;border:1px solid var(--blue);color:var(--blue);font-size:10px;text-align:center;line-height:24px}

.section-title{position:absolute;font-family:'Oswald',Arial,sans-serif;font-size:17px;font-weight:500;text-transform:uppercase;color:var(--ink);border-bottom:1px solid var(--line);padding-bottom:8px}
.section-title::after{content:"";position:absolute;left:0;bottom:-1px;width:40px;height:2px;background:var(--blue)}

.post{position:absolute;left:22px;width:780px;height:178px;border-bottom:1px solid var(--line);display:flex;gap:20px}
.post-photo{width:150px;height:158px;flex:none}
.post-body{flex:1;position:relative}
.post-body h4{font-family:'Oswald',Arial,sans-serif;font-size:14px;font-weight:500;text-transform:uppercase}
.post-body .by{font-size:10px;color:var(--muted)}
.post-body p{color:var(--muted);font-size:11.5px;margin-top:34px}
.price{position:absolute;right:0;top:0;text-align:right;font-size:10px;color:var(--muted)}
.price b{display:block;font-family:'Oswald',Arial,sans-serif;font-size:24px;font-weight:500;color:var(--blue);line-height:1.1}

.news{position:absolute;left:838px;width:260px;display:flex;gap:12px}
.date{width:42px;flex:none;text-align:center;font-family:'Oswald',Arial,sans-serif;color:var(--blue);line-height:1}
.date b{font-size:30px;font-weight:500;display:block}
.date span{font-size:11px;text-transform:uppercase;color:var(--muted)}
.news p{font-size:11.5px;color:var(--muted)}
.news p strong{color:var(--ink);font-weight:600}
.quote{position:absolute;left:838px;top:950px;width:260px;border:1px solid var(--line);padding:14px;color:var(--muted);font-size:11.5px}
.quote-name{position:absolute;left:838px;top:1078px;font-size:11px;color:var(--blue);font-weight:600;line-height:1.5}
.quote-name span{display:block;color:var(--muted);font-weight:400}

.partners{position:absolute;left:22px;top:1130px;width:1076px;height:60px;border-top:1px solid var(--line);display:flex;justify-content:space-between;align-items:center;padding:0 20px}
.partner{display:flex;align-items:center;gap:8px;font-size:22px;font-weight:600;color:#6b747c}
.partner i{width:22px;height:22px;background:#6b747c;border-radius:50%;display:block}
.partner i.sq{border-radius:3px}

/* footer */
.footer{position:absolute;left:0;top:1850px;width:1200px;height:342px;background:var(--blue);color:var(--white)}
.fcol{position:absolute;top:34px;width:240px}
.fcol h5{font-family:'Oswald',Arial,sans-serif;font-size:16px;font-weight:500;margin-bottom:14px}
.fcol p{font-size:11px;opacity:.92}
.socials{display:flex;gap:8px;margin-top:16px}
.socials i{width:28px;height:28px;border-radius:50%;background:var(--blue-deep);display:block}
.tweet{display:flex;gap:10px;margin-bottom:14px}
.tweet i{width:14px;height:14px;flex:none;background:var(--white);opacity:.8;margin-top:3px}
.tweet a{color:#d6f0fb;display:block}
.thumbs{display:grid;grid-template-columns:repeat(3,70px);gap:8px}
.thumb{height:58px}
.contact-row{display:flex;gap:10px;font-size:11px;margin-bottom:10px}
.contact-row svg{flex:none;margin-top:2px}
.bottombar{position:absolute;left:0;top:2192px;width:1200px;height:60px;background:var(--blue-dark);color:var(--white);display:flex;align-items:center;justify-content:space-between;padding:0 40px;font-size:11px}
.bottombar nav{display:flex;gap:40px}
</style>
</head>
<body>

<header class="hero">
  <div class="hero-photo" role="img" aria-label="Photo of a tropical island with palm trees in turquoise sea under a blue sky"></div>
  <div class="topbar">
    <div class="select">USD $ <span>▾</span></div>
    <div class="select">ENGLISH <span>▾</span></div>
  </div>
  <div class="logo">CALDERA KEY</div>
  <nav class="nav">
    <a class="active">Home</a><a>About Us</a><a>Services</a><a>Gallery</a><a>Blog</a><a>Contact Us</a>
  </nav>
  <div class="welcome">
    <h1>Welcome to Caldera Key</h1>
    <p>We will be targeting tourism in a small town in central Panama</p>
  </div>
</header>

<main class="panel">
  <div class="cards">
    <article class="card">
      <h3>Selling Guided Tours</h3>
      <div class="card-photo" role="img" aria-label="Photo of a tropical tour location" style="background:linear-gradient(180deg,#8fd0ef,#3a9fc9)"></div>
      <p>It is a long established fact that a reader will be distracted by the readable content of a page when looking at its layout and design.</p>
      <div class="card-meta">◷ 358 booking current tours</div>
      <div class="bar"><span style="width:55%;background:var(--green)"></span></div>
      <div class="stats">
        <div class="stat"><b>356</b>Likes</div><div class="stat"><b>48</b>Views</div><div class="stat"><b>24</b>Tours</div>
        <div class="details">Details</div>
      </div>
    </article>
    <article class="card">
      <h3>Hotel/Hostels</h3>
      <div class="card-photo" role="img" aria-label="Photo of a hotel pool at dusk" style="background:linear-gradient(180deg,#1d3f6b,#4fa9d6)"></div>
      <p>It is a long established fact that a reader will be distracted by the readable content of a page when looking at its layout and design.</p>
      <div class="card-meta">◷ 358 booking current rooms</div>
      <div class="bar"><span style="width:40%;background:var(--orange)"></span></div>
      <div class="stats">
        <div class="stat"><b>356</b>Likes</div><div class="stat"><b>48</b>Views</div><div class="stat"><b>24</b>Rooms</div>
        <div class="details">Details</div>
      </div>
    </article>
    <article class="card">
      <h3>Rental Vehicles</h3>
      <div class="card-photo" role="img" aria-label="Photo of a family beside a red rental car" style="background:linear-gradient(180deg,#d9e4ec,#b9c9d4)"></div>
      <p>It is a long established fact that a reader will be distracted by the readable content of a page when looking at its layout and design.</p>
      <div class="card-meta">◷ 358 booking current cars</div>
      <div class="bar"><span style="width:65%;background:var(--blue)"></span></div>
      <div class="stats">
        <div class="stat"><b>356</b>Likes</div><div class="stat"><b>48</b>Views</div><div class="stat"><b>24</b>Cars</div>
        <div class="details">Details</div>
      </div>
    </article>
  </div>

  <h2 class="section-title" style="left:22px;top:462px;width:780px">Latest Post</h2>

  <article class="post" style="top:512px">
    <div class="post-photo" role="img" aria-label="Photo of a city waterfront skyline" style="background:linear-gradient(180deg,#7fb6dc,#2d4d66)"></div>
    <div class="post-body">
      <h4>Contrary to Popular</h4><div class="by">By: Spring Lorem Ipsum</div>
      <div class="price">Start From<b>$ 49.90</b></div>
      <p>It is a long established fact that a reader will be distracted by the readable content of a page when looking at its layout. The point of using Lorem Ipsum is that it has a more normal distribution of letters, making it look like readable English.</p>
    </div>
  </article>
  <article class="post" style="top:712px">
    <div class="post-photo" role="img" aria-label="Photo of a harbour with city towers" style="background:linear-gradient(180deg,#9cc7e6,#36607f)"></div>
    <div class="post-body">
      <h4>Contrary to Popular</h4><div class="by">By: Spring Lorem Ipsum</div>
      <div class="price">Start From<b>$ 49.90</b></div>
      <p>It is a long established fact that a reader will be distracted by the readable content of a page when looking at its layout. The point of using Lorem Ipsum is that it has a more normal distribution of letters, making it look like readable English.</p>
    </div>
  </article>
  <article class="post" style="top:912px">
    <div class="post-photo" role="img" aria-label="Photo of modern city towers" style="background:linear-gradient(180deg,#c6d8e6,#4a5d6f)"></div>
    <div class="post-body">
      <h4>Contrary to Popular</h4><div class="by">By: Spring Lorem Ipsum</div>
      <div class="price">Start From<b>$ 49.90</b></div>
      <p>It is a long established fact that a reader will be distracted by the readable content of a page when looking at its layout. The point of using Lorem Ipsum is that it has a more normal distribution of letters, making it look like readable English.</p>
    </div>
  </article>

  <h2 class="section-title" style="left:838px;top:462px;width:260px">Latest News</h2>
  <div class="news" style="top:512px">
    <div class="date"><b>27</b><span>Sept</span></div>
    <p><strong>Lorem ipsum dolor sit amet, tours and leisure activities ...</strong><br>It is a long established fact that a reader will be distracted by the readable content of a page when looking at its layout.</p>
  </div>
  <div class="news" style="top:640px">
    <div class="date"><b>27</b><span>Sept</span></div>
    <p><strong>Lorem ipsum dolor sit amet, tours and leisure activities ...</strong><br>It is a long established fact that a reader will be distracted by the readable content of a page when looking at its layout.</p>
  </div>

  <h2 class="section-title" style="left:838px;top:900px;width:260px">What Client Saying</h2>
  <blockquote class="quote">It is a long established fact that a reader will be distracted by the readable content of a page when looking at its layout. The point of using Lorem Ipsum is that it has a more normal distribution of letters.</blockquote>
  <div class="quote-name">Name - Country Name<span>Traveller since 2014</span></div>

  <div class="partners">
    <div class="partner"><i></i>Sonora</div>
    <div class="partner"><i class="sq"></i>Quadrel</div>
    <div class="partner">Picturo</div>
    <div class="partner">Lensvault</div>
    <div class="partner"><i class="sq"></i>Tessel</div>
    <div class="partner">Picturo</div>
  </div>
</main>

<footer class="footer">
  <div class="fcol" style="left:40px">
    <h5>Stay in Touch</h5>
    <p>Follow us on social channels to get the latest tours, travel news and special offers from the island.</p>
    <div class="socials"><i></i><i></i><i></i><i></i><i></i></div>
  </div>
  <div class="fcol" style="left:330px">
    <h5>Latest Tweets</h5>
    <div class="tweet"><i></i><p>New island tours are open for booking this season. <a>calderakey.example/tours</a></p></div>
    <div class="tweet"><i></i><p>Check our latest travel guide for the central valley. <a>calderakey.example/news</a></p></div>
  </div>
  <div class="fcol" style="left:620px">
    <h5>Snapline Photos</h5>
    <div class="thumbs">
      <div class="thumb" role="img" aria-label="Beach photo" style="background:linear-gradient(#8fd3f0,#2ab3b8)"></div>
      <div class="thumb" role="img" aria-label="Island photo" style="background:linear-gradient(#6fb5de,#3f8a48)"></div>
      <div class="thumb" role="img" aria-label="Coast photo" style="background:linear-gradient(#a9dcef,#e7e2cf)"></div>
      <div class="thumb" role="img" aria-label="City photo" style="background:linear-gradient(#9cc7e6,#36607f)"></div>
      <div class="thumb" role="img" aria-label="Hotel photo" style="background:linear-gradient(#2e6fa3,#1d3f6b)"></div>
      <div class="thumb" role="img" aria-label="Lagoon photo" style="background:linear-gradient(#7fd6d0,#2a9fb0)"></div>
    </div>
  </div>
  <div class="fcol" style="left:910px">
    <h5>Contact Us</h5>
    <div class="contact-row"><svg width="10" height="14" viewBox="0 0 10 14"><path d="M5 0a5 5 0 0 1 5 5c0 4-5 9-5 9S0 9 0 5a5 5 0 0 1 5-5z" fill="#fff"/><circle cx="5" cy="5" r="2" fill="#1e9bd7"/></svg><span>Address: 14 Calle Ribera, Valle Norte,<br>Central Province</span></div>
    <div class="contact-row"><svg width="12" height="12" viewBox="0 0 12 12"><path d="M2 0l3 3-1.5 1.5a7 7 0 0 0 4 4L9 7l3 3-2 2C5 12 0 7 0 2z" fill="#fff"/></svg><span>Phone: +00 123 456 7890</span></div>
    <div class="contact-row"><svg width="12" height="10" viewBox="0 0 12 10"><rect width="12" height="10" fill="#fff"/><path d="M0 0l6 5 6-5" stroke="#1e9bd7" fill="none"/></svg><span>Email: hello@calderakey.example</span></div>
  </div>
</footer>
<div class="bottombar">
  <nav><span>Home</span><span>About Us</span><span>Services</span><span>Gallery</span><span>Blog</span><span>Contact Us</span></nav>
  <span>© Copyright 2015 Caldera Key All Rights Reserved</span>
</div>

</body>
</html>
```